Need business card with a logo for a hearing aid sales and audiology business. We have two Hearing Instrument Specialists and one Audiologist on staff. Over 25 years in business. Locally owned and operated. Financing available. Most insurances accepted.

Summit Audio Wellness LLC
48730 W Larchmont, Suite 7
Spokane, WA 99281
509-617-2084
www.summitaudiowell.example

Manager
Tobias Kerrell HIS COHC
License #71829046

Target Market(s)

50yr old + people with a hearing loss.

Industry/Entity Type

Business

Contact Information for Business Card

48730 W Larchmont, Suite 7
Spokane, WA 99281
509-617-2084
www.summitaudiowell.example

Manager
Tobias Kerrell HIS COHC
NLVE #71829046

Font styles to use
Serif
Sans Serif

Requirements
Must have
• Business name, Tobias's name and title(s) and contact information, License #, web address

```html
<!DOCTYPE html>
<html lang="en">
<head>
<meta charset="utf-8">
<title>Summit Audio Wellness LLC – Business Card</title>
<link rel="stylesheet" href="https://fonts.googleapis.com/css2?family=Alegreya+Sans:ital,wght@0,400;0,500;0,700;1,400&family=Alegreya+Sans+SC:wght@500&family=Open+Sans:wght@400&display=swap">
<style>
  :root {
    --slate-blue: #5a77a0;
    --ink-blue: #2b4c9b;
    --sky-blue: #1a9fe0;
    --rule-grey: #ececec;
    --card-white: #ffffff;
  }
  html, body {
    margin: 0;
    padding: 0;
    overflow: hidden;
    background: var(--card-white);
  }
  .card {
    position: relative;
    width: 1200px;
    height: 758px;
    background: var(--card-white);
    overflow: hidden;
    font-family: "Alegreya Sans", sans-serif;
  }
  .brand-square {
    position: absolute;
    left: 39px;
    top: 0;
    width: 198px;
    height: 265px;
    background: var(--slate-blue);
  }
  .company-name {
    position: absolute;
    left: 272px;
    top: 72px;
    margin: 0;
    font-size: 63px;
    font-weight: 500;
    letter-spacing: -0.5px;
    color: var(--slate-blue);
    white-space: nowrap;
    line-height: 1;
  }
  .title-rule {
    position: absolute;
    left: 314px;
    top: 177px;
    width: 776px;
    height: 3px;
    background: var(--rule-grey);
  }
  .person {
    position: absolute;
    left: 55px;
    top: 380px;
    width: 520px;
    text-align: center;
  }
  .person-name {
    margin: 0;
    font-size: 49px;
    font-weight: 700;
    color: var(--ink-blue);
    line-height: 1;
    white-space: nowrap;
  }
  .person-role {
    margin: 8px 0 0;
    font-family: "Alegreya Sans SC", sans-serif;
    font-weight: 500;
    font-size: 34px;
    color: var(--sky-blue);
    line-height: 1;
    letter-spacing: 1px;
  }
  .person-license {
    font-family: "Alegreya Sans", sans-serif;
    font-style: italic;
    font-weight: 400;
    font-size: 23px;
    letter-spacing: 0;
  }
  .contact {
    position: absolute;
    left: 663px;
    top: 380px;
    color: var(--ink-blue);
    font-family: "Alegreya Sans SC", sans-serif;
    font-weight: 500;
    font-size: 34px;
    line-height: 1.3;
  }
  .contact-row {
    display: flex;
    align-items: center;
  }
  .contact-row + .contact-row {
    margin-top: 14px;
  }
  .contact-icon {
    width: 56px;
    flex: none;
    margin-right: 12px;
  }
  .contact-text {
    margin: 0;
    white-space: nowrap;
    font-style: normal;
  }
  .footer-band {
    position: absolute;
    left: 0;
    bottom: 0;
    width: 1200px;
    height: 66px;
    background: var(--slate-blue);
  }
  .website {
    position: absolute;
    right: 31px;
    top: 12px;
    font-family: "Open Sans", sans-serif;
    font-size: 34px;
    color: var(--card-white);
    line-height: 1;
  }
</style>
</head>
<body>
  <div class="card">
    <div class="brand-square"></div>
    <h1 class="company-name">Summit Audio Wellness LLC</h1>
    <div class="title-rule"></div>

    <div class="person">
      <p class="person-name">Tobias Kerrell HIS COHC</p>
      <p class="person-role">Manager <span class="person-license">(NLVE #71829046)</span></p>
    </div>

    <div class="contact">
      <div class="contact-row">
        <svg class="contact-icon" viewBox="0 0 56 44" aria-hidden="true">
          <path d="M4 14 C4 4 52 4 52 14 L52 18 L42 18 L40 12 L16 12 L14 18 L4 18 Z" fill="var(--ink-blue)"/>
          <path d="M16 16 L40 16 L46 40 L10 40 Z" fill="var(--ink-blue)"/>
          <g fill="var(--card-white)">
            <rect x="20" y="22" width="4" height="3"/><rect x="26" y="22" width="4" height="3"/><rect x="32" y="22" width="4" height="3"/>
            <rect x="20" y="27" width="4" height="3"/><rect x="26" y="27" width="4" height="3"/><rect x="32" y="27" width="4" height="3"/>
            <rect x="20" y="32" width="4" height="3"/><rect x="26" y="32" width="4" height="3"/><rect x="32" y="32" width="4" height="3"/>
          </g>
        </svg>
        <p class="contact-text">Tel: 509-617-2084</p>
      </div>
      <div class="contact-row">
        <svg class="contact-icon" viewBox="0 0 56 52" aria-hidden="true">
          <path d="M4 26 L28 4 L52 26" fill="none" stroke="var(--ink-blue)" stroke-width="6" stroke-linejoin="round"/>
          <path d="M11 26 L28 11 L45 26 L45 50 L33 50 L33 36 L23 36 L23 50 L11 50 Z" fill="var(--ink-blue)"/>
        </svg>
        <address class="contact-text">48730 W Larchmont, Suite 7<br>Spokane, WA 99281</address>
      </div>
    </div>

    <div class="footer-band">
      <span class="website">www.summitaudiowell.example</span>
    </div>
  </div>
</body>
</html>
```